Business Card Design

We are a commercial real estate brokerage in San Francisco, leasing office buildings downtown.
I would like a clean, elegant look. Simple but powerful .

Industry/Entity Type

Business

Contact Information for Business Card

Derek Holloway
lic# 07258143
415.555.0172
derek@velt-commercial.example
velt-commercial.example

```html
<!DOCTYPE html>
<html lang="en">
<head>
<meta charset="utf-8">
<title>Velt Commercial – Business Card</title>
<link rel="stylesheet" href="https://fonts.googleapis.com/css2?family=Open+Sans:wght@400;600;700&display=swap">
<style>
  :root {
    --canvas: #e8e6e3;
    --card-dark: #0d0e10;
    --card-light: #f4f4f4;
    --panel-grey: #55585b;
    --accent-blue: #6c82a3;
    --ink: #2f3237;
    --ink-soft: #55585b;
    --brand-light: #8fa0b8;
    --white: #ffffff;
  }
  * { margin: 0; padding: 0; box-sizing: border-box; }
  html, body { width: 1200px; height: 768px; overflow: hidden; }
  body {
    background: var(--canvas);
    font-family: "Open Sans", Arial, sans-serif;
    position: relative;
  }
  .card {
    position: absolute;
    top: 230px;
    width: 540px;
    height: 309px;
    border-radius: 4px;
    overflow: hidden;
    box-shadow: 0 6px 18px rgba(0,0,0,0.18);
  }
  .card--back { left: 40px; background: var(--card-dark); }
  .card--front { left: 620px; background: var(--card-light); }

  .brand {
    position: absolute;
    display: flex;
    align-items: center;
    gap: 12px;
    font-family: "Open Sans", Arial, sans-serif;
    font-weight: 600;
    white-space: nowrap;
  }
  .brand__dot { width: 14px; height: 14px; border-radius: 50%; flex: none; }

  .card--back .brand { left: 0; right: 0; top: 136px; justify-content: center; font-size: 34px; color: var(--brand-light); }
  .card--back .brand__dot { background: var(--brand-light); }

  .card--front .brand { left: 66px; top: 58px; font-size: 30px; color: var(--ink); }
  .card--front .brand__dot { background: var(--accent-blue); }

  .card__swoosh { position: absolute; inset: 0; }

  .contact {
    position: absolute;
    left: 66px;
    top: 132px;
    color: var(--ink);
  }
  .contact__name { font-size: 17px; font-weight: 700; }
  .contact__title { font-size: 9.5px; color: var(--ink-soft); margin-bottom: 14px; }
  .contact__list { list-style: none; font-size: 11px; }
  .contact__list li { display: flex; align-items: center; gap: 9px; height: 17px; }
  .contact__list svg { width: 10px; height: 10px; flex: none; }

  .licence {
    position: absolute;
    right: 26px;
    bottom: 20px;
    font-size: 12px;
    color: var(--white);
    letter-spacing: 0.5px;
  }
</style>
</head>
<body>

  <section class="card card--back" aria-label="Business card back">
    <p class="brand"><span class="brand__dot"></span>Velt Commercial</p>
  </section>

  <section class="card card--front" aria-label="Business card front">
    <svg class="card__swoosh" viewBox="0 0 540 309" aria-hidden="true">
      <path d="M440,0 C525,120 440,245 240,309 L540,309 L540,0 Z" fill="var(--panel-grey)"/>
      <path d="M418,6 C500,125 420,238 228,302" fill="none" stroke="var(--accent-blue)" stroke-width="5" stroke-linecap="round"/>
      <path d="M402,12 C476,125 400,230 214,296" fill="none" stroke="var(--accent-blue)" stroke-width="1.5"/>
    </svg>

    <p class="brand"><span class="brand__dot"></span>Velt Commercial</p>

    <div class="contact">
      <p class="contact__name">Derek Holloway</p>
      <p class="contact__title">Managing Director</p>
      <ul class="contact__list">
        <li>
          <svg viewBox="0 0 10 10"><path d="M1,3 Q5,0 9,3 L8,4.5 L6.5,3.8 L6.5,3 Q5,2.5 3.5,3 L3.5,3.8 L2,4.5 Z M2.5,5 H7.5 L8.5,9 H1.5 Z" fill="var(--ink-soft)"/></svg>
          415.555.0172
        </li>
        <li>
          <svg viewBox="0 0 10 10"><rect x="0.5" y="2" width="9" height="6.5" fill="var(--ink-soft)"/><path d="M0.5,2 L5,6 L9.5,2" fill="none" stroke="var(--card-light)" stroke-width="0.9"/></svg>
          derek@velt-commercial.example
        </li>
        <li>
          <svg viewBox="0 0 10 10"><circle cx="5" cy="5" r="4.3" fill="none" stroke="var(--ink-soft)" stroke-width="1"/><ellipse cx="5" cy="5" rx="1.8" ry="4.3" fill="none" stroke="var(--ink-soft)" stroke-width="0.8"/><path d="M0.7,5 H9.3" stroke="var(--ink-soft)" stroke-width="0.8"/></svg>
          www.velt-commercial.example
        </li>
      </ul>
    </div>

    <p class="licence">LIC# 07258143</p>
  </section>

</body>
</html>
```